Meridale Bed Company Needs Business Card

Looking for a very nice looking business card. Creative but not extravagant. We sell beds and pillows across the U.S. and need something professional but catchy. I have attached the logo.

Name : Devin Holt
Title : President
Phone : (800) 471-2960
Email: sleep@quilmora.com
Website: www.quilmora.com

Can be single-sided or double-sided
horizontal or vertical

Can use Blues/Greys

Target Market(s)

Mass Market

Industry/Entity Type

Retail

Contact Information for Business Card

Name : Devin Holt
Title : President
Phone : (800) 471-2960
Email: sleep@quilmora.com
Website: www.quilmora.com

Requirements
Must have
• Clean, Modern, Smooth
• Can use Blues/Greys
• On the other side without the information - have something simple like www.quilmora.com or our logo
Nice to have
• Surprise me
Should not have
• Nothing crazy, nothing cluttered

```html
<!DOCTYPE html>
<html lang="en">
<head>
<meta charset="utf-8">
<title>Quilmora Business Card</title>
<link href="https://fonts.googleapis.com/css2?family=Lato:wght@300;400;700&display=swap" rel="stylesheet">
<style>
  :root {
    --backdrop: #1e1e1e;
    --card: #f4f4f4;
    --card-edge: #e2e2e2;
    --brand-blue: #2a94cc;
    --band-blue: #2a8cbf;
    --ink: #2b2b2b;
    --band-text: #e9f4fa;
  }
  html, body {
    margin: 0;
    padding: 0;
    width: 1200px;
    height: 873px;
    overflow: hidden;
    background: var(--backdrop);
    font-family: "Lato", Arial, sans-serif;
  }
  .business-card {
    position: absolute;
    left: 180px;
    top: 196px;
    width: 840px;
    height: 480px;
    border-radius: 24px;
    overflow: hidden;
    background: linear-gradient(135deg, #fbfbfb 0%, var(--card) 55%, var(--card-edge) 100%);
    box-shadow: 0 20px 50px rgba(0,0,0,0.55);
  }
  .brand-name {
    position: absolute;
    left: 86px;
    top: 178px;
    margin: 0;
    font-weight: 300;
    font-size: 84px;
    letter-spacing: 2px;
    color: var(--brand-blue);
    line-height: 1;
  }
  .divider {
    position: absolute;
    left: 470px;
    top: 70px;
    width: 2px;
    height: 270px;
    background: linear-gradient(to bottom, rgba(42,148,204,0.9), rgba(42,148,204,0));
  }
  .contact-block {
    position: absolute;
    left: 505px;
    top: 92px;
  }
  .person-name {
    margin: 0;
    font-weight: 700;
    font-size: 28px;
    color: var(--brand-blue);
  }
  .person-title {
    margin: 2px 0 0 8px;
    font-size: 18px;
    color: var(--ink);
  }
  .contact-list {
    list-style: none;
    margin: 22px 0 0 18px;
    padding: 0;
  }
  .contact-item {
    display: flex;
    align-items: center;
    gap: 10px;
    font-size: 20px;
    color: var(--ink);
    margin-bottom: 14px;
  }
  .contact-icon {
    width: 22px;
    height: 18px;
    flex: none;
  }
  .web-band {
    position: absolute;
    left: 0;
    bottom: 0;
    width: 100%;
    height: 86px;
    background: var(--band-blue);
    display: flex;
    align-items: flex-start;
    justify-content: center;
  }
  .web-address {
    margin-top: 12px;
    font-weight: 700;
    font-size: 18px;
    letter-spacing: 4px;
    color: var(--band-text);
  }
</style>
</head>
<body>
  <div class="business-card">
    <h1 class="brand-name">quilmora</h1>
    <div class="divider"></div>
    <div class="contact-block">
      <p class="person-name">Devin Holt</p>
      <p class="person-title">President</p>
      <ul class="contact-list">
        <li class="contact-item">
          <svg class="contact-icon" viewBox="0 0 22 18" aria-hidden="true">
            <path d="M2 6 Q11 0 20 6 L18 8 L15 6 L15 4 Q11 3 7 4 L7 6 L4 8 Z" fill="#2a94cc"/>
            <rect x="5" y="9" width="12" height="8" rx="2" fill="#2a94cc"/>
            <circle cx="11" cy="13" r="2" fill="#f4f4f4"/>
          </svg>
          <span>(800) 471-2960</span>
        </li>
        <li class="contact-item">
          <svg class="contact-icon" viewBox="0 0 22 18" aria-hidden="true">
            <rect x="1" y="2" width="20" height="14" fill="#2a94cc"/>
            <path d="M1 2 L11 10 L21 2" fill="none" stroke="#f4f4f4" stroke-width="1.6"/>
          </svg>
          <span>sleep@quilmora.com</span>
        </li>
      </ul>
    </div>
    <div class="web-band">
      <span class="web-address">www.quilmora.com</span>
    </div>
  </div>
</body>
</html>
```